Flyer für eine Tagespflege (Senioren & Demenzkranke)
Zielgruppe
Hallo wir sind eine Tagespflege die 365 Tage im Jahr geöffnet hat. Wir kümmern uns um Senioren und Demenzkranke. Zielgruppe sind Personen die Ihre Angehörigen (zur Entlastung) Zuhause pflegen und Senioren die den Tag in Gemeinschaft verbringen wollen und abends zu Hause im eigenen Bett schlafen wollen
Aufgabenstellung
Es sollte ansprechend bzw. hochwertig aussehen. Es sollte ein Standard Format sein. Bei der Größe gibt es keine Vorgabe. Es sollte übersichtlich sein. Die Adresse sollte mit Karte dargestellt sein. Das wir 365 Tage im Jahr geöffnet haben muss klar hervor gehen.

```html
<!DOCTYPE html>
<html lang="de">
<head>
<meta charset="utf-8">
<title>Tagespflege – Flyer DIN lang</title>
<link href="https://fonts.googleapis.com/css2?family=Roboto+Condensed:wght@700&family=Source+Sans+3:ital,wght@0,400;0,600;0,700;1,600&display=swap" rel="stylesheet">
<style>
:root{
  --green:#2a8a2e;
  --green-soft:#e3efdc;
  --cream:#fbf3d6;
  --paper:#ffffff;
  --stage:#ebe7e8;
  --fold:#d9d6d6;
  --map:#e9ecee;
}
*{box-sizing:border-box;margin:0;padding:0}
html,body{width:995px;height:1200px;overflow:hidden}
body{background:var(--stage);font-family:"Source Sans 3",sans-serif;color:var(--green);position:relative}
.spread{position:absolute;left:227px;width:540px;height:572px;display:flex;box-shadow:0 2px 6px rgba(0,0,0,.12)}
.spread--outside{top:20px}
.spread--inside{top:608px}
.panel{position:relative;width:270px;height:572px;background:var(--paper);overflow:hidden}
.panel+.panel{border-left:1px solid var(--fold)}
.photo{position:absolute}
.heading{position:absolute;left:20px;font-weight:700;font-size:14.5px;line-height:1;color:var(--green)}
.copy{position:absolute;left:20px;width:230px;font-size:10.9px;line-height:13.8px;color:var(--green);hyphens:auto;-webkit-hyphens:auto}
.copy em{font-weight:600;font-style:italic}
.phone-line{position:absolute;left:0;width:270px;display:flex;justify-content:center;align-items:center;gap:8px;font-weight:700;font-size:20px;line-height:1;color:var(--green)}
.phone-line svg{width:20px;height:16px}

/* Photo areas: calm two-tone fills */
.tone-office{background:radial-gradient(ellipse at 30% 70%,#c9d9b8 0%,rgba(201,217,184,0) 60%),linear-gradient(180deg,#eef0ef 0%,#dfe3e1 100%)}
.tone-care{background:radial-gradient(ellipse at 75% 70%,#9bb58a 0%,rgba(155,181,138,0) 55%),linear-gradient(180deg,#f3eadb 0%,#e8dcc6 100%)}
.tone-room{background:linear-gradient(180deg,#f7ecd6 0%,#f0dcb8 60%,#e2c79d 100%)}
.tone-garden{background:radial-gradient(ellipse at 30% 40%,#b9d0a1 0%,rgba(185,208,161,0) 60%),linear-gradient(180deg,#a7c28c 0%,#8fae76 100%)}
.tone-reading{background:radial-gradient(ellipse at 60% 60%,#f4ead9 0%,rgba(244,234,217,0) 60%),linear-gradient(180deg,#e6ebe2 0%,#eadcc2 100%)}

/* Team panel */
.team-photo{left:20px;top:24px;width:250px;height:117px;border-radius:10px 0 0 10px}
.email-line{position:absolute;left:0;top:407px;width:270px;display:flex;justify-content:center;align-items:center;gap:5px;font-weight:700;font-size:11.5px;line-height:1}
.email-line svg{width:14px;height:11px}
.address-box{position:absolute;left:0;top:437px;width:256px;height:111px;border:1px solid var(--green);border-left:none;border-radius:0 10px 10px 0;overflow:hidden}
.address-map{position:absolute;left:0;top:0;width:153px;height:111px;background:var(--map)}
.address-text{position:absolute;left:166px;top:9px;font-size:8.8px;line-height:11.5px}
.address-text h3{font-size:13px;font-weight:700;line-height:1;margin-bottom:7px}

/* Cover panel */
.brand{position:absolute;left:0;top:23px;width:270px;text-align:center}
.brand-mark{display:block;margin:0 auto;width:92px;height:92px;border-radius:50%;background:var(--green-soft)}
.brand-title{font-family:"Roboto Condensed",sans-serif;font-weight:700;font-size:34px;letter-spacing:.3px;margin-top:10px;line-height:1}
.brand-name{font-size:12.5px;letter-spacing:.6px;margin-top:7px;line-height:1}
.cover-rule{position:absolute;left:0;top:195px;width:270px;height:2px;background:var(--green)}
.cover-photo{left:0;top:197px;width:270px;height:142px}
.claim{position:absolute;left:0;top:339px;width:270px;height:65px;background:var(--cream);text-align:center;padding-top:8px}
.claim-main{font-weight:700;font-size:27px;line-height:1}
.claim-sub{font-size:22px;line-height:1.1}
.cover-room{left:0;top:404px;width:270px;height:122px;border-bottom:2px solid var(--green)}

/* Inside spread */
.care-photo{left:0;top:267px;width:258px;height:137px;border-radius:0 12px 12px 0}
.dayclub-box{position:absolute;left:20px;top:421px;width:251px;height:134px;border:1px solid var(--green);border-right:none;border-radius:10px 0 0 10px;padding:16px 12px 0 15px}
.dayclub-box .title{font-weight:700;font-size:14.5px;line-height:1;margin-bottom:9px}
.dayclub-box .copy{position:static;width:222px}
.services-photo{left:19px;top:34px;width:251px;height:173px;border-radius:12px 0 0 12px}
.room-photo{left:0;top:421px;width:252px;height:134px;border:1px solid var(--green);border-left:none;border-radius:0 10px 10px 0}
</style>
</head>
<body>

<section class="spread spread--outside">
  <article class="panel panel-team">
    <div class="photo team-photo tone-office" role="img" aria-label="Foto: Mitarbeiterin lächelnd am Schreibtisch im Büro"></div>
    <h2 class="heading" style="top:154px">Unser Team</h2>
    <div class="copy" style="top:180px">
      <p>„Hand in Hand“, das ist die Devise unseres Teams aus 16 freundlichen Mitarbeitern. Gemeinsam sind wir täglich für unsere Klienten im Einsatz. Kranke und hilfebedürftige Menschen zu unterstützen, ist für uns nicht nur ein Job, sondern eine Herzensangelegenheit. Wir möchten Ihnen und Ihren Angehörigen das Leben ein Stück leichter und schöner gestalten. Kompetent und respektvoll begleiten wir Ihr Leben in Ihrem Zuhause.</p>
    </div>
    <div class="copy" style="top:326px;width:170px">
      <p>Rufen Sie uns an und lassen sich unverbindlich beraten:</p>
    </div>
    <div class="phone-line" style="top:369px">
      <svg viewBox="0 0 20 16" aria-hidden="true"><path fill="currentColor" d="M1 5c0-2 3-3.5 9-3.5S19 3 19 5v1.5h-4.5V4.8C12 4.3 8 4.3 5.5 4.8v1.7H1z"/><path fill="currentColor" d="M4 8l2.5-3h7L16 8v7H4z"/><circle cx="10" cy="10.5" r="2" fill="#fff"/></svg>
      <span>039740 55120</span>
    </div>
    <div class="email-line">
      <svg viewBox="0 0 14 11" aria-hidden="true"><rect x="1" y="1" width="12" height="9" fill="none" stroke="currentColor" stroke-width="1.3"/><path d="M1 1l6 5 6-5" fill="none" stroke="currentColor" stroke-width="1.3"/></svg>
      <span>henrike.wollanek@pflegepost.de</span>
    </div>
    <div class="address-box">
      <div class="address-map" role="img" aria-label="Kartenausschnitt mit dem Standort des Pflegedienstes"></div>
      <div class="address-text">
        <h3>Adresse</h3>
        Ambulanter<br>Pflegedienst<br>Henrike Wollanek<br>Am Lindenweg 7<br>17390 Falkenried/<br>OT Brunnow
      </div>
    </div>
  </article>

  <article class="panel panel-cover">
    <header class="brand">
      <span class="brand-mark" aria-hidden="true"></span>
      <h1 class="brand-title">TAGESPFLEGE</h1>
      <p class="brand-name">Henrike Wollanek</p>
    </header>
    <div class="cover-rule"></div>
    <div class="photo cover-photo tone-care" role="img" aria-label="Foto: Pflegerin im Gespräch mit einer Seniorin"></div>
    <div class="claim">
      <div class="claim-main">365 Tage im Jahr</div>
      <div class="claim-sub">für Sie da!</div>
    </div>
    <div class="photo cover-room tone-room" role="img" aria-label="Foto: heller Aufenthaltsraum der Tagespflege mit Tischen"></div>
    <div class="phone-line" style="top:538px">
      <svg viewBox="0 0 20 16" aria-hidden="true"><path fill="currentColor" d="M1 5c0-2 3-3.5 9-3.5S19 3 19 5v1.5h-4.5V4.8C12 4.3 8 4.3 5.5 4.8v1.7H1z"/><path fill="currentColor" d="M4 8l2.5-3h7L16 8v7H4z"/><circle cx="10" cy="10.5" r="2" fill="#fff"/></svg>
      <span>039740 55120</span>
    </div>
  </article>
</section>

<section class="spread spread--inside">
  <article class="panel panel-care">
    <h2 class="heading" style="top:38px;left:35px">Pflege mit Herz</h2>
    <div class="copy" style="top:61px;left:35px;width:208px">
      <p>Sie möchten weiterhin in <em>Ihrem Zuhause leben</em>, Selbstbestimmung und Lebensqualität genießen und benötigen dabei Unterstützung? Gemeinsam mit Ihnen besprechen wir ein für Sie passendes Leistungs- und Serviceangebot nach Ihren Wünschen und Bedürfnissen.</p>
      <p>Seit der Eröffnung unseres Pflegedienstes 1996 konnten wir in Falkenried und im Umkreis von rund 20 Kilometern zahlreiche Klienten liebevoll umsorgen.</p>
      <p>Zögern Sie nicht, uns persönlich zu kontaktieren, wir beraten Sie gerne individuell mit Herz und Sachverstand.</p>
    </div>
    <div class="photo care-photo tone-garden" role="img" aria-label="Foto: Pflegerin und älterer Herr im Garten"></div>
    <div class="dayclub-box">
      <h2 class="title">Unsere Tagespflege</h2>
      <div class="copy">Sie fühlen sich in Ihrem Zuhause wohl möchten oder können dort aber nicht den gesamten Tag über alleine sein? Unsere Tagespflege bietet Ihnen behaglich eingerichtete Räumlichkeiten, nette Gesellschaft und Abwechslung.</div>
    </div>
  </article>

  <article class="panel panel-services">
    <div class="photo services-photo tone-reading" role="img" aria-label="Foto: Seniorin liest Zeitung, Pflegerin schaut zu"></div>
    <h2 class="heading" style="top:218px;left:19px">Leistungen</h2>
    <div class="copy" style="top:241px;left:19px;width:232px">
      <p>Das selbstständige Wohnen im <em>eigenen Zuhause</em> bis ins hohe Alter steht bei Senioren ganz oben auf der Wunschliste.</p>
      <p>Mit unserer häuslichen Kranken- und Seniorenpflege sorgen wir dafür, dass dieser Wunsch für Sie Wirklichkeit werden kann.</p>
      <p>Entscheiden Sie selbst oder in Absprache mit Ihren Angehörigen, wie viel Hilfe Sie benötigen. Gerne stellen wir Ihnen das Serviceangebot unseres ambulanten Pflegedienstes vor und informieren Sie über Kosten sowie die Leistungen der Krankenkassen.</p>
    </div>
    <div class="photo room-photo tone-room" role="img" aria-label="Foto: Aufenthaltsraum der Tagespflege mit Obstkorb"></div>
  </article>
</section>

</body>
</html>
```